Design for schnapps bottle label "Río Ámbar"

Hi! On a small land lot we are producing our own Italian schnapps "Grappa". For the bottles we would like to modernize our current labes that you find below. The two cats looking at each other should remain, but updated and more modern. I am very much looking forward to your suggestions. Best, Jens

Target Market(s)

Schnapps bottle label

Requirements
Must have
• Cats should resemble the cats that are decorating the house entry (see attached), however, should have a more modern appearance.

Text elements should remain: "Grappa", "Río Ámbar", "Legnoso", "[Vintage Year], "Raccolta No", "Vol %"
Should not have
• Current ornament can be used, replaced or deleted (whatever looks best)

```html
<!DOCTYPE html>
<html lang="it">
<head>
<meta charset="utf-8">
<title>Grappa legnoso 2015 – Río Ámbar</title>
<link rel="stylesheet" href="https://fonts.googleapis.com/css2?family=Federant&family=Allura&family=Cormorant+Garamond:wght@500&display=swap">
<style>
  :root {
    --backdrop: #161616;
    --cream: #ece7df;
    --cream-shade: #e2dcd2;
    --ink: #1f1f1f;
    --rust: #8a3219;
    --band-red: #d8431f;
    --band-orange: #ec8a2e;
    --rule-black: #141414;
  }
  * { box-sizing: border-box; margin: 0; padding: 0; }
  html, body {
    width: 900px; height: 1200px; overflow: hidden;
    background: var(--backdrop);
  }
  .canvas {
    width: 900px; height: 1200px;
    display: flex; align-items: center; justify-content: center;
  }
  .label {
    width: 534px; height: 1160px;
    display: flex; flex-direction: column;
  }
  .band-top {
    height: 36px;
    background: linear-gradient(90deg, var(--band-red), #e05a25 50%, var(--band-red));
    border-bottom: 5px solid var(--band-orange);
  }
  .label-body {
    height: 1000px;
    background: linear-gradient(180deg, var(--cream), var(--cream-shade));
    position: relative;
    text-align: center;
  }
  .product-name {
    position: absolute; top: 78px; left: 0; right: 0;
    font-family: "Federant", serif;
    font-size: 142px; line-height: 1;
    color: var(--ink);
    text-shadow: 0 2px 3px rgba(0,0,0,.25);
  }
  .edition {
    position: absolute; top: 318px; left: 0; right: 0;
    color: var(--rust);
  }
  .edition .style {
    font-family: "Allura", cursive; font-size: 46px;
  }
  .edition .year {
    font-family: "Cormorant Garamond", serif; font-size: 34px; font-weight: 500;
  }
  .maker-link {
    position: absolute; top: 386px; left: 0; right: 0;
    font-family: "Allura", cursive; font-size: 34px; color: var(--rust);
  }
  .cats-art {
    position: absolute; top: 458px; left: 22px; right: 22px; height: 200px;
    background: radial-gradient(ellipse at center, #3a3a3a 0%, #2a2a2a 55%, var(--cream) 80%);
    opacity: .85;
  }
  .brand-name {
    position: absolute; top: 722px; left: 0; right: 0;
    font-family: "Federant", serif; font-size: 78px; line-height: 1;
    color: var(--rust);
  }
  .details {
    position: absolute; bottom: 32px; left: 26px; right: 26px;
    display: flex; justify-content: space-between; align-items: baseline;
    color: var(--rust);
  }
  .details .batch {
    font-family: "Allura", cursive; font-size: 32px;
  }
  .details .batch .num, .details .abv {
    font-family: "Cormorant Garamond", serif; font-size: 30px; font-weight: 500;
  }
  .rule-black {
    height: 20px;
    background: var(--rule-black);
  }
  .band-bottom {
    flex: 1;
    background: linear-gradient(90deg, var(--band-red), var(--band-orange) 45%, var(--band-red));
  }
</style>
</head>
<body>
  <main class="canvas">
    <article class="label">
      <div class="band-top" role="img" aria-label="Red and orange decorative pattern band"></div>
      <section class="label-body">
        <h1 class="product-name">Grappa</h1>
        <p class="edition"><span class="style">“legnoso”</span><span class="year">2015</span></p>
        <p class="maker-link">di</p>
        <div class="cats-art" role="img" aria-label="Illustration of two black cat silhouettes stretching toward each other"></div>
        <h2 class="brand-name">Río Ámbar</h2>
        <footer class="details">
          <span class="batch">Raccolta No. <span class="num">01</span></span>
          <span class="abv">41.0 Vol</span>
        </footer>
      </section>
      <div class="rule-black"></div>
      <div class="band-bottom" role="img" aria-label="Red and orange decorative pattern band with cat silhouettes"></div>
    </article>
  </main>
</body>
</html>
```